Bright Harbor Charity - helping the disadvantaged

I would like a new web site design for my charity BRIGHT HARBOR. The charity provides help for the disadvantaged. See current site
brightharbor.org.au for details. Please refer to the current site for information on the charity. The objectives of the charity are in the "about us" tab. You will also notice on the site that we provide information about events that we sponsor an area for this should be provided on the site.

Target Market(s)

We have two targets:
1. Individuals and Businesses that will donate money to the charity.
2. Individuals that are in need of support from the charity.

Industry/Entity Type

Charity

Requirements
Must have
• Ability for individuals to be able to understand the type of support we can provide.
Nice to have
• Our logo should be prominate on each pages
Should not have
• Should be use modern fonts

```html
<!DOCTYPE html>
<html lang="en">
<head>
<meta charset="utf-8">
<title>Bright Harbor – Harmony Day</title>
<link href="https://fonts.googleapis.com/css2?family=Arimo:ital,wght@0,400;0,700;1,400&display=swap" rel="stylesheet">
<style>
:root{
  --page:#cdc9bd;
  --panel:#fcf9ee;
  --panel-edge:#e3ddcc;
  --frame:#d7d1bb;
  --nav:#8a6c12;
  --body-text:#7b756a;
  --heading:#1f4a22;
  --accent:#f0a050;
  --button:#e5e0d3;
  --button-text:#7a7468;
  --dot:#b30d0d;
  --logo:#6fb43c;
  --banner-dark:#221208;
  --white:#ffffff;
}
*{box-sizing:border-box;margin:0;padding:0}
html,body{width:984px;height:1200px;overflow:hidden}
body{background:var(--page);font-family:"Arimo",Arial,sans-serif;position:relative}
.box{position:absolute;background:var(--panel);border:1px solid var(--panel-edge);border-radius:6px;box-shadow:0 0 8px rgba(0,0,0,.08)}
.nav-bar{left:46px;top:20px;width:645px;height:55px}
.main-nav{position:absolute;left:33px;top:19px;display:flex;font-size:12.5px;color:var(--nav)}
.main-nav span{padding:0 6px}
.main-nav span.sep{padding:0 2px}
.search-bar{left:690px;top:20px;width:246px;height:55px}
.search-field{position:absolute;left:28px;top:12px;width:190px;height:26px;border:1px solid #d9d3c3;border-radius:8px;background:var(--white);box-shadow:inset 0 1px 2px rgba(0,0,0,.1)}
.search-field span{position:absolute;right:6px;top:5px;font-size:12px;color:#555;border-left:1px solid #999;padding-left:4px;line-height:14px}
.banner-frame{position:absolute;left:46px;top:74px;width:889px;height:233px;background:var(--frame)}
.banner{position:absolute;left:54px;top:84px;width:870px;height:213px;background:radial-gradient(ellipse 260px 160px at 180px 90px,#d8d2cc 0%,#6d5a4c 45%,var(--banner-dark) 80%),var(--banner-dark)}
.banner-photo{position:absolute;left:560px;top:0;width:310px;height:213px;background:radial-gradient(ellipse 150px 110px at 190px 110px,#d9b79a 0%,#8a6248 45%,#2a170b 100%)}
.logo{position:absolute;left:30px;top:88px;font-size:40px;font-weight:400;color:var(--logo);letter-spacing:1px}
.content{left:46px;top:325px;width:645px;height:814px}
.sidebar{left:690px;top:325px;width:246px;height:814px}
.announce{position:absolute;left:26px;top:19px;font-size:12px;color:#2b2b2b}
.announce-link{position:absolute;left:27px;top:38px;font-size:12.5px;color:var(--accent)}
.btn{position:absolute;background:var(--button);color:var(--button-text);font-style:italic;font-size:12px;display:flex;align-items:center;justify-content:center}
.divider{position:absolute;left:74px;top:61px;width:490px;border-top:1px dashed #d6d0c2}
.photo{position:absolute;box-shadow:2px 3px 5px rgba(0,0,0,.35)}
.photo-swing{left:65px;top:77px;width:472px;height:290px;background:radial-gradient(ellipse 200px 140px at 230px 140px,#e9c3a8 0%,#c07a4a 35%,#4b7a3a 70%,#2e4a22 100%)}
.photo-banner{left:27px;top:518px;width:560px;height:117px;background:linear-gradient(180deg,#000 0%,#000 60%,#2a2418 100%)}
.excerpt{position:absolute;left:28px;width:580px;font-size:12.5px;line-height:18px;color:var(--body-text)}
.event-head{position:absolute;left:15px;top:15px;font-size:13px;font-weight:700;line-height:14px;color:var(--heading)}
.feature-list{position:absolute;left:16px;top:93px;list-style:none;font-size:12px;color:#4a4a4a}
.feature-list li{height:24px;padding-left:12px;position:relative}
.feature-list li.dotted::before{content:"";position:absolute;left:0;top:4px;width:6px;height:6px;border-radius:50%;background:#555}
.side-title{position:absolute;left:13px;font-size:13.5px;font-weight:700;color:var(--heading);display:flex;align-items:center}
.side-title::before{content:"";width:10px;height:10px;border-radius:50%;background:var(--dot);margin-right:8px}
.art{left:9px;top:311px;width:198px;height:133px;background:radial-gradient(circle at 50% 50%,#f1c24a 0%,#b8411a 40%,#6b1a0c 100%)}
.harmony{position:absolute;left:9px;top:560px;width:198px;height:68px;background:linear-gradient(90deg,#c7ab90,#d9cf3a,#e68dc0,#e2772a,#35b8b0)}
.tagline{position:absolute;left:44px;top:638px;width:130px;text-align:center;font-size:12.5px;font-weight:700;color:#111;border-bottom:1px solid #111;padding-bottom:3px}
.copyright{position:absolute;right:51px;top:1150px;font-size:10.5px;font-weight:700;color:var(--white)}
</style>
</head>
<body>
<div class="box nav-bar">
  <nav class="main-nav">
    <span>Home</span><span class="sep">|</span><span>About Us</span><span class="sep">|</span><span>Donate</span><span class="sep">|</span><span>Apply</span><span class="sep">|</span><span>Pledge</span><span class="sep">|</span><span>Nominate</span><span class="sep">|</span><span>Events</span><span class="sep">|</span><span>Contact Us</span><span class="sep">|</span><span>Directors</span>
  </nav>
</div>
<div class="box search-bar"><div class="search-field"><span>Search</span></div></div>

<div class="banner-frame"></div>
<header class="banner">
  <div class="banner-photo" role="img" aria-label="Smiling toddler wearing feathered angel wings, leaning on a wicker basket"></div>
  <div class="logo">BRIGHT HARBOR</div>
</header>

<main class="box content">
  <div class="announce">ANNOUNCEMENT:</div>
  <div class="announce-link">Harmony Day Information sheet &amp; Booking form</div>
  <div class="btn" style="left:314px;top:31px;width:90px;height:24px">Click to view</div>
  <div class="divider"></div>

  <div class="photo photo-swing" role="img" aria-label="Red-haired girl smiling on a playground swing"></div>
  <p class="excerpt" style="top:386px">Harmony Day Event 2012 Harmony Celebration Day - "EVERYONE BELONGS" Date:Satyurday 24th March 2012&nbsp; Venue: Lindale Care Education Facilities, Maple Road, Ashvale. Time: 10am - 3 pm Harmony.Bright Harbor &amp; Lindale Care will be holding a multicultural market and art exhibition combined with a community harmony day being held on site at....</p>
  <div class="btn" style="left:29px;top:467px;width:90px;height:24px">Read more</div>

  <div class="photo photo-banner" role="img" aria-label="Harmony Day 24 March banner with a row of colourful figures holding hands"></div>
  <p class="excerpt" style="top:661px">Harmony Day Event 2012 Harmony Celebration Day - "EVERYONE BELONGS" Date:Satyurday 24th March 2012&nbsp; Venue: Lindale Care Education Facilities, Maple Road, Ashvale. Time: 10am - 3 pm Harmony.Bright Harbor &amp; Lindale Care will be holding a multicultural market and art exhibition combined with a community harmony day being held on site at....</p>
  <div class="btn" style="left:29px;top:743px;width:90px;height:24px">Read more</div>
</main>

<aside class="box sidebar">
  <h2 class="event-head">Saturday 24th March<br>at Lindale Care Education<br>Facilities Maple &amp; Ridge<br>Roads Ashvale</h2>
  <ul class="feature-list">
    <li class="dotted">Lots of prizes to be Won!</li>
    <li class="dotted">Free Entry &amp; variety of free activities</li>
    <li class="dotted">Art Exhibition</li>
    <li class="dotted">Perfomance</li>
    <li class="dotted">Community service Info stalls</li>
    <li class="dotted">Multicultural food market stalls</li>
    <li>Multural arts &amp; craft market stalls.</li>
  </ul>
  <h3 class="side-title" style="top:279px">Art Exhibition</h3>
  <div class="photo art" role="img" aria-label="Dot painting artwork in red, yellow and white"></div>
  <div class="btn" style="left:13px;top:473px;width:90px;height:24px">Read more</div>
  <h3 class="side-title" style="top:531px">Harmony Day</h3>
  <div class="harmony" role="img" aria-label="Colourful figures holding hands"></div>
  <div class="tagline">everyone Belongs</div>
  <div class="btn" style="left:13px;top:683px;width:90px;height:24px">Read more</div>
</aside>

<footer class="copyright">Copyright © 2012 Bright Harbor Proprietary Limited. All Rights Reserved.</footer>
</body>
</html>
```